One pager digital ad-Corporate travel Manager

I need a design that is smooth, and business like. I don’t like basic generic designs that I can make my self. I’m looking for a sharp clean ad that clearly was made by a great designer. I need some bullet points in and the add to be clean. Here is a list of some content from our content writers. You can arrange and play with the words a bit.

*Budget*- having a travel management service will ensure that your company sticks to a budget which will help PROTECT your bottom line. Travel expenses often CAN BE COSTLY and having a SAVVY corporate travel manager handle YOUR TRAVEL ARRANGEMENTS will make sure that the travel expenses are kept under control.
*Efficiency- time *is money. Have your staff focus on their core business and have the corporate travel manager handle all the logistics for their travel including airfare, hotel cars and events TO MAXIMIZE EFFICIENCY AND KEEP YOUR STAFF FOCUSED ON YOUR CORE BUSINESS

*unforeseen circumstances* – the corporate travel manager handleS any cancellations, missed flights, canceled flights. Quick rebooking, and repositioning, and dealing with getting credits and reimbursement is extremely difficult and time-consuming. The corporate travel manager handles all of that SO YOU CAN CONTINUE ON SCHEDULE WITHOUT SPENDING HOURS REBOOKING AND GETTING CREDIT

Efficient and organized business travel management-help reduce travel expenses, streamline expense reports, optimize booking processes, and make managing the corporate travel experience way easier for all stakeholders involved.

Travel Support

Report on travel spend: In order to optimize their budgets, businesses need to know which departments are spending what on travel. Agencies can report on spend for all stakeholders by team, department, or project, and help you accurately track all your travel expenses.

Maintain compliance: Every company has some sort of rules that make up their travel policy. An agency can enforce these guidelines when booking.

Velnor Trips is a global leader in business travel management services. We drive savings, efficiency and safety to businesses and their travelers all around the world.

If you are looking for a tailored travel management solution, delivering customer service excellence, and a demonstrable return on investment, then you’ve come to the right place

Corporate travel policy compliance
Travel management reports
Meetings and event management
Travel program management
Dedicated travel counselor teams

By listening to your needs and focusing on your goals we can help your company design a global corporate travel service program that controls costs, improves traveler satisfaction and fits your corporate culture.

Our qualified business travel agents and cutting-edge technology deliver solutions that provide the best travel arrangements and travel policy adherence in the business. From CEO to support staff, our services can help make corporate travel a more efficient and enjoyable experience for everyone involved.

With so much involved in travel – from booking and expenses to meetings and strategy – you need the backing of a proven leader…
Velnor Trips, We’re your corporate travel partner to help you manage it all.

```html
<!DOCTYPE html>
<html lang="en">
<head>
<meta charset="UTF-8">
<title>Velnor Trips – Corporate Travel Management</title>
<link href="https://fonts.googleapis.com/css2?family=Montserrat:wght@400;500;600;700&display=swap" rel="stylesheet">
<style>
  :root {
    --navy: #10204a;
    --navy-panel: rgba(14, 27, 58, 0.94);
    --ink: #1c2444;
    --white: #ffffff;
    --backdrop: #e7e8ea;
    --sky-top: #5f9fd6;
    --sky-light: #cfe4f4;
    --sea: #4fb3c9;
    --sand: #e4c898;
    --skyline: #c9ced8;
  }
  * { margin: 0; padding: 0; box-sizing: border-box; }
  html, body { width: 1050px; height: 1200px; overflow: hidden; }
  body {
    background: var(--backdrop);
    font-family: "Montserrat", Arial, sans-serif;
    color: var(--ink);
    position: relative;
  }
  .page {
    position: absolute;
    top: 246px;
    width: 500px;
    height: 707px;
    background: var(--white);
    overflow: hidden;
    box-shadow: 0 4px 14px rgba(0,0,0,0.18);
  }
  .page--front { left: 17px; }
  .page--back { left: 533px; }
  .photo { position: absolute; }

  /* Front page */
  .beach-photo {
    left: 0; top: 0; width: 500px; height: 335px;
    background: linear-gradient(180deg, var(--sky-top) 0%, #9cc9ea 38%, var(--sky-light) 50%, var(--sea) 56%, #a8dbe0 61%, var(--sand) 70%, #cfa877 100%);
  }
  .brand-name {
    position: absolute; left: 0; width: 264px; top: 96px; text-align: center;
    font-size: 17px; font-weight: 500; letter-spacing: 0.5px; color: var(--navy);
  }
  .benefit-panel {
    position: absolute; left: 0; top: 187px; width: 282px; height: 277px;
    background: var(--navy-panel); color: var(--white);
  }
  .benefit-block { position: absolute; left: 19px; width: 246px; }
  .benefit-block--budget { top: 20px; }
  .benefit-block--efficiency { top: 158px; }
  .benefit-title {
    font-size: 12.5px; font-weight: 500; letter-spacing: 0.6px; margin-bottom: 10px;
  }
  .benefit-text {
    font-size: 9.3px; line-height: 11.2px; margin-bottom: 10px;
  }
  .benefit-text strong { font-weight: 700; }
  .balloon-photo {
    left: 287px; top: 337px; width: 213px; height: 117px;
    background: linear-gradient(170deg, #f2b66c 0%, #c97a55 40%, #6b5a4a 70%, #3f5236 100%);
  }
  .lake-photo {
    left: 287px; top: 457px; width: 213px; height: 117px;
    background: linear-gradient(180deg, #c4cfd3 0%, #6a7c6e 38%, #2f5d4a 52%, #3db8c4 70%, #7dd3d8 100%);
  }
  .circumstances {
    position: absolute; left: 19px; top: 478px; width: 252px;
  }
  .circumstances-title {
    font-size: 11.5px; font-weight: 700; color: var(--navy); letter-spacing: 0.3px;
  }
  .circumstances-text {
    font-size: 9.3px; line-height: 11.2px; margin-top: 1px;
  }
  .circumstances-text + .circumstances-text { margin-top: 10px; }
  .circumstances-text strong { font-weight: 700; color: var(--navy); }

  .skyline {
    left: 0; top: 590px; width: 500px; height: 117px;
    background: linear-gradient(180deg, rgba(255,255,255,0) 0%, var(--skyline) 55%, rgba(255,255,255,0.6) 100%);
  }
  .web-address {
    position: absolute; left: 0; width: 500px; top: 681px;
    text-align: center; font-size: 13px; font-weight: 700; letter-spacing: 1.2px; color: var(--navy);
  }

  /* Back page */
  .island-photo {
    left: 0; top: 0; width: 500px; height: 341px;
    background: linear-gradient(180deg, #bcd8ee 0%, #e6f0f8 36%, #cfe6f3 48%, #7fb8d3 58%, #4e9a8a 70%, #5e8f4e 84%, #b6c9b0 100%);
  }
  .section-heading {
    position: absolute; left: 20px; top: 23px;
    font-size: 15px; font-weight: 600; color: var(--navy); letter-spacing: 0.4px;
  }
  .intro-col {
    position: absolute; top: 52px; font-size: 9.3px; line-height: 11.1px;
  }
  .intro-col--left { left: 20px; width: 252px; }
  .intro-col--right { left: 287px; width: 206px; }
  .intro-col p + p { margin-top: 9px; }
  .intro-col strong { font-weight: 700; color: var(--navy); }
  .services-panel {
    position: absolute; left: 0; top: 341px; width: 154px; height: 206px;
    background: var(--navy); color: var(--white);
    padding: 22px 8px 0 17px;
  }
  .services-list { list-style: none; }
  .services-list li {
    position: relative; padding-left: 8px;
    font-size: 8.8px; font-weight: 600; line-height: 11px; letter-spacing: 0.2px;
    margin-bottom: 14px;
  }
  .services-list li::before {
    content: ""; position: absolute; left: 0; top: 4px;
    width: 2.5px; height: 2.5px; border-radius: 50%; background: var(--white);
  }
  .river-photo { left: 157px; top: 343px; width: 112px; height: 60px; background: linear-gradient(180deg, #3c5a3c 0%, #4d7a6a 60%, #2f6e74 100%); }
  .city-photo { left: 272px; top: 343px; width: 112px; height: 60px; background: linear-gradient(160deg, #9fb9a8 0%, #d2c7a4 55%, #7e9a86 100%); }
  .cliff-photo { left: 387px; top: 343px; width: 113px; height: 60px; background: linear-gradient(180deg, #e8a77e 0%, #9c8aa8 45%, #4a5a78 70%, #2e3240 100%); }
  .closing {
    position: absolute; left: 165px; top: 415px; width: 324px;
    font-size: 9.2px; line-height: 11.8px; text-align: justify;
  }
  .closing p + p { margin-top: 11px; }
  .closing .lead-out { font-weight: 500; color: var(--navy); }
  .closing .partner-line {
    margin-top: 13px; font-size: 9.8px; font-weight: 700; color: var(--navy);
    line-height: 15px; letter-spacing: 0.3px; text-align: justify;
  }
</style>
</head>
<body>

<section class="page page--front">
  <div class="photo beach-photo" role="img" aria-label="Sunny tropical beach with a wicker lounge daybed and sun loungers under palms"></div>

  <div class="brand-name">Velnor Trips</div>

  <div class="benefit-panel">
    <div class="benefit-block benefit-block--budget">
      <h2 class="benefit-title">*BUDGET*-</h2>
      <p class="benefit-text">having a travel management service will ensure that your company sticks to a budget which will help <strong>PROTECT</strong> your bottom line.</p>
      <p class="benefit-text">Travel expenses often CAN BE COSTLY and having a SAVVY corporate travel manager handle <strong>YOUR TRAVEL ARRANGEMENTS</strong> will make sure that the travel expenses are kept under control.</p>
    </div>
    <div class="benefit-block benefit-block--efficiency">
      <h2 class="benefit-title">*EFFICIENCY-</h2>
      <p class="benefit-text">time *is money. Have your staff focus on their core business and have the corporate travel manager handle all the logistics for their travel including airfare, hotel cars and events <strong>TO MAXIMIZE EFFICIENCY AND KEEP YOUR STAFF FOCUSED ON YOUR CORE BUSINESS</strong></p>
    </div>
  </div>

  <div class="photo balloon-photo" role="img" aria-label="Hot air balloons over misty mountains at sunrise"></div>
  <div class="photo lake-photo" role="img" aria-label="Turquoise mountain lake with canoes and pine forest"></div>

  <div class="circumstances">
    <h2 class="circumstances-title">*UNFORESEEN CIRCUMSTANCES* –</h2>
    <p class="circumstances-text">the corporate travel manager handleS any cancellations, missed flights, canceled flights. Quick rebooking, and repositioning, and dealing with getting credits and reimbursement is extremely difficult and time-consuming.</p>
    <p class="circumstances-text">The corporate travel manager handles all of that <strong>SO YOU CAN CONTINUE ON SCHEDULE WITHOUT SPENDING HOURS REBOOKING AND GETTING CREDIT</strong></p>
  </div>

  <div class="photo skyline" role="img" aria-label="Faded skyline of world landmarks"></div>
  <div class="web-address">www.velnortrips.com</div>
</section>

<section class="page page--back">
  <div class="photo island-photo" role="img" aria-label="Traveller in a sun hat overlooking a tropical island bay"></div>

  <h1 class="section-heading">TRAVEL SUPPORT</h1>

  <div class="intro-col intro-col--left">
    <p><strong>Report on travel spend:</strong> In order to optimize their budgets, businesses need to know which departments are spending what on travel. Agencies can report on spend for all stakeholders by team, department, or project, and help you accurately track all your travel expenses.</p>
    <p><strong>Maintain compliance:</strong> Every company has some sort of rules that make up their travel policy. An agency can enforce these guidelines when booking.</p>
  </div>

  <div class="intro-col intro-col--right">
    <p>Velnor Trips is a global leader in business travel management services. We drive savings, efficiency and safety to businesses and their travelers all around the world.</p>
    <p>If you are looking for a tailored travel management solution, delivering customer service excellence, and a demonstrable return on investment, then you’ve come to the right place.</p>
  </div>

  <div class="services-panel">
    <ul class="services-list">
      <li>CORPORATE TRAVEL POLICY COMPLIANCE</li>
      <li>TRAVEL MANAGEMENT REPORTS</li>
      <li>MEETINGS AND EVENT MANAGEMENT</li>
      <li>TRAVEL PROGRAM MANAGEMENT</li>
      <li>DEDICATED TRAVEL COUNSELOR TEAMS</li>
    </ul>
  </div>

  <div class="photo river-photo" role="img" aria-label="Traveller on a wooden boat in a jungle river"></div>
  <div class="photo city-photo" role="img" aria-label="Traveller holding a map on a city street"></div>
  <div class="photo cliff-photo" role="img" aria-label="Hiker sitting on a rock above a bay at sunset"></div>

  <div class="closing">
    <p>By listening to your needs and focusing on your goals we can help your company design a global corporate travel service program that controls costs, improves traveler satisfaction and fits your corporate culture.</p>
    <p>Our qualified business travel agents and cutting-edge technology deliver solutions that provide the best travel arrangements and travel policy adherence in the business. From CEO to support staff, our services can help make corporate travel a more efficient and enjoyable experience for everyone involved.</p>
    <p class="lead-out">With so much involved in travel – from booking and expenses to meetings and strategy – you need the backing of a proven leader…</p>
    <p class="partner-line">VELNOR TRIPS, WE’RE YOUR CORPORATE TRAVEL PARTNER TO HELP YOU MANAGE IT ALL.</p>
  </div>

  <div class="photo skyline" role="img" aria-label="Faded skyline of world landmarks"></div>
  <div class="web-address">www.velnortrips.com</div>
</section>

</body>
</html>
```